Krelvomi.com - have media you dont own! Krelvomi the stars - Site Concept

KRELVOMI those who ENTERTAIN you, who you LISTEN to, who you IDOLISE, and who you 'BORROW' from... KRELVOMI the STARS the things that are the STARS... see brief concept at www.krelvomi.com

Looking for site concept, something new, very simple transaction, not generic website. Must also drive mobile app download call to action.

In principle, we dont care how you get your media or watch a TV series or download your favourite song, however, if you are honest and love the song/movie/servies or the star, pay them!
The solution should include anonymous/protected end user interaction and digital certificate/rights management process for end users who have media not paid for to krelvomi and receive an approved digital certificate from Krelvomi authorised by the relevant media house proving legal ownership of the digital media item (music, video, TV series/episode, movie etc...)

Basic functions:
Consumer: Mobile and Web
Personal media rights administration
1. Capture core data – Create secure and private Profile account
2. Log owned/borrowed media (media legally owned tagged and media 'borrowed' tagged, decision criteria, pledge or purchase (open to ideas, function to browse PC for media on HDD/Tunovex or mobile, tag ones to pay for etc, capture CD's owned etc. create digital library filing system?)
3. Pledge payment for media - future payment value linked to market value, I like this, not sure I will keep it forever though, pay less? use once?
4. Purchase rights for media - payment based on market value of related media item. (zapcoin, credit card or other?)
5. Media Certificate management - secure and PRIVATE distribution of the certificate (open to options here), approved by media house.

design ideas welcome, modern, fast, simple steps, engaging, with sense of privacy, we wont share data, we will just pay the media houses more! Based in Switzerland, managed by Swiss privacy law. transact with min personal data required.

Reason: The service committed to 50+ designs, most received are form one provider, all off the mark and very basic, not impressed so far, was expecting some real design thought rather than standard templates being rehashed, thats not deisgn? Hope in next days I am impressed?

Target Market(s)

Digital Media Consumer

Industry/Entity Type

Media

Number of Pages Required

5+ page

Font styles to use
Sans Serif

Requirements
Must have
• Must have privacy by design, must have simple and minimal steps taken to log and declare media items and pay, with no risk of exposure. Must have payment process, must have interface to easily load media into site, drag drop, search HDD/mobile etc.
Nice to have
• Digital certificate process and admin interaction of site and with media house, secure and trusted process to provide report and logs of payment for media to specific media house and relevant payments made and tracked.
Should not have
• complex workflows are out, complex payment methods.

```html
<!DOCTYPE html>
<html lang="en">
<head>
<meta charset="utf-8">
<title>Krelvomi.com – Site Concept</title>
<link href="https://fonts.googleapis.com/css2?family=Open+Sans:wght@400;600;700;800&display=swap" rel="stylesheet">
<style>
:root{
  --orange:#f39a1f;
  --ink:#333;
  --muted:#8a8a8a;
  --dark:#1d1d1d;
  --panel:#2a2a2a;
  --line:#3a3a3a;
  --footer:#181818;
  --white:#fff;
}
*{box-sizing:border-box;margin:0;padding:0}
html,body{width:696px;height:1200px;overflow:hidden;background:#fff}
body{font-family:"Open Sans",Arial,sans-serif;color:var(--ink);position:relative}
.hero{position:absolute;left:0;top:0;width:696px;height:352px;background:#3b3b3b;overflow:hidden}
.hero-photo{position:absolute;inset:0;background:radial-gradient(ellipse 210px 260px at 470px 200px,#a57a5c 0%,#6b4d3a 38%,#3d3a38 70%,#2b2b2b 100%)}
.site-header{position:absolute;top:0;left:0;width:100%;height:46px;background:rgba(0,0,0,.45);display:flex;align-items:center;justify-content:space-between;padding:0 24px}
.logo{color:var(--white);font-weight:700;font-size:17px;letter-spacing:.3px}
.nav{display:flex;gap:18px;list-style:none}
.nav li{color:#ddd;font-size:7px;letter-spacing:.6px}
.nav li.active{color:var(--orange)}
.hero-copy{position:absolute;left:58px;top:84px;width:220px;color:var(--white)}
.hero-copy h1{font-size:24px;font-weight:700;margin-bottom:10px}
.hero-copy p{font-size:7.5px;line-height:13px;color:#e4e4e4;margin-bottom:18px}
.btn{display:inline-block;background:var(--orange);color:var(--white);font-size:7px;font-weight:700;letter-spacing:.5px;padding:7px 16px;border-radius:2px}
.slide-arrow{position:absolute;top:178px;width:16px;height:26px}
.slide-arrow.prev{left:8px}.slide-arrow.next{right:8px}
.intro{position:absolute;top:370px;left:0;width:100%;text-align:center}
.intro h2{font-size:13px;font-weight:600;color:#333}
.intro p{font-size:6.5px;line-height:10px;color:var(--muted);width:430px;margin:6px auto 0}
.cards{position:absolute;top:420px;left:24px;display:flex;gap:11px}
.card{width:131px;height:172px;border:1px solid #e2e2e2;background:#fff}
.card-photo{height:82px}
.card-photo.one{background:linear-gradient(135deg,#c99868,#6a4a33)}
.card-photo.two{background:linear-gradient(135deg,#8fa5c0,#3e4f67)}
.card-photo.three{background:linear-gradient(135deg,#d8a05a,#3a2a22)}
.card-body{padding:10px;text-align:center}
.card-body p{font-size:6.5px;line-height:10px;color:#666}
.stars{margin-top:8px;color:var(--orange);font-size:8px;letter-spacing:1px}
.feature-list{position:absolute;top:420px;left:452px;width:220px;height:172px;background:var(--panel);list-style:none;padding:8px 14px}
.feature-list li{font-size:6.5px;color:#bbb;height:19.5px;line-height:19.5px;border-bottom:1px solid var(--line);padding-left:12px;position:relative}
.feature-list li:last-child{border-bottom:none}
.feature-list li::before{content:"";position:absolute;left:0;top:8px;width:4px;height:4px;background:var(--orange)}
.stars-band{position:absolute;top:614px;left:0;width:100%;height:188px;overflow:hidden}
.stars-band-photo{position:absolute;inset:0;background:radial-gradient(ellipse 260px 120px at 348px 188px,#6b4a2c 0%,#2b2119 55%,#121212 100%)}
.stars-band-copy{position:absolute;inset:0;text-align:center;padding-top:52px;color:var(--white)}
.stars-band-copy h2{font-size:22px;font-weight:800;letter-spacing:.5px}
.stars-band-copy p{font-size:7px;line-height:11px;color:#ccc;width:360px;margin:6px auto 14px}
.newsletter{position:absolute;top:826px;left:0;width:100%;height:130px;padding:0 24px}
.newsletter-head{display:flex;align-items:center;gap:8px;margin-top:28px}
.newsletter-head h3{font-size:12px;font-weight:600;color:#333;letter-spacing:.3px}
.newsletter-text{font-size:6.5px;line-height:10px;color:var(--muted);width:220px;margin-top:8px}
.signup{position:absolute;left:300px;top:36px;display:flex}
.signup .field{width:250px;height:24px;border:1px solid #ddd;font-size:6.5px;color:#aaa;padding:0 10px;line-height:22px}
.signup .btn{height:24px;line-height:10px;margin-left:4px;padding:7px 18px}
.site-footer{position:absolute;top:980px;left:0;width:100%;height:220px;background:var(--footer);color:#aaa}
.footer-cols{display:flex;padding:22px 24px 0;gap:0}
.footer-col{width:162px}
.footer-col h4{font-size:8px;color:var(--white);font-weight:600;letter-spacing:.4px;margin-bottom:12px}
.event{display:flex;gap:6px;margin-bottom:9px}
.event-thumb{width:20px;height:16px;background:#555}
.event p,.post p{font-size:5.5px;line-height:8px;color:#999}
.post{display:flex;gap:6px;margin-bottom:9px}
.post-box{width:8px;height:8px;border:1px solid #888;flex:none;margin-top:1px}
.links{list-style:none}
.links li{font-size:6px;color:#999;line-height:12px}
.contact-row{display:flex;align-items:center;gap:6px;font-size:6px;color:#999;line-height:9px;margin-bottom:8px}
.copyright{position:absolute;bottom:0;left:0;width:100%;height:20px;border-top:1px solid #2c2c2c;text-align:center;font-size:5.5px;line-height:20px;color:#777}
</style>
</head>
<body>
<section class="hero">
  <div class="hero-photo" role="img" aria-label="Photo of a young woman listening to music on large headphones"></div>
  <header class="site-header">
    <div class="logo">KRELVOMI.COM</div>
    <ul class="nav">
      <li class="active">HOME</li><li>ITEMS</li><li>MUSIC</li><li>MOVIES</li><li>VIDEOS</li><li>BLOG</li><li>CONTACT</li>
    </ul>
  </header>
  <div class="hero-copy">
    <h1>KRELVOMI.COM</h1>
    <p>KRELVOMI those who ENTERTAIN you, who you LISTEN to, who you IDOLISE, and who you 'BORROW' from. Pay the stars for the media you love.</p>
    <span class="btn">DOWNLOAD OUR FAVOURITE ITEMS</span>
  </div>
  <svg class="slide-arrow prev" viewBox="0 0 16 26"><path d="M12 3 3 13l9 10" fill="none" stroke="#fff" stroke-width="2"/></svg>
  <svg class="slide-arrow next" viewBox="0 0 16 26"><path d="M4 3l9 10-9 10" fill="none" stroke="#fff" stroke-width="2"/></svg>
</section>

<section class="intro">
  <h2>Time to show respect, appreciation, honour and 'whatever', just KRELVOMI</h2>
  <p>An anonymous service for music, movies, TV and digital entertainment lovers, who acquire their media freely online and who would like to pay their respects to the artists they appreciate by paying them.</p>
</section>

<div class="cards">
  <article class="card">
    <div class="card-photo one" role="img" aria-label="Photo of a music fan"></div>
    <div class="card-body"><p>Lorem ipsum dolor sit amet, consectetur adipiscing</p><div class="stars">★★★☆☆</div></div>
  </article>
  <article class="card">
    <div class="card-photo two" role="img" aria-label="Photo of friends sharing media"></div>
    <div class="card-body"><p>Lorem ipsum dolor sit amet, consectetur adipiscing</p><div class="stars">★★★☆☆</div></div>
  </article>
  <article class="card">
    <div class="card-photo three" role="img" aria-label="Photo of a performer on stage"></div>
    <div class="card-body"><p>Lorem ipsum dolor sit amet, consectetur adipiscing</p><div class="stars">★★★☆☆</div></div>
  </article>
</div>

<ul class="feature-list">
  <li>Log in privately to your media library</li>
  <li>Declare owned and borrowed items</li>
  <li>Drag and drop files from any device</li>
  <li>Pledge a payment for later</li>
  <li>Purchase rights at market value</li>
  <li>Receive an approved certificate</li>
  <li>Lorem ipsum dolor sit amet</li>
  <li>Lorem ipsum dolor sit amet</li>
</ul>

<section class="stars-band">
  <div class="stars-band-photo" role="img" aria-label="Photo of a concert crowd with raised hands under stage lights"></div>
  <div class="stars-band-copy">
    <h2>KRELVOMI YOUR STARS</h2>
    <p>anonymously and receive a digital certificate validating and legalizing your digital rights to the media you freely obtained or viewed online.</p>
    <span class="btn">PAY NOW</span>
  </div>
</section>

<section class="newsletter">
  <div class="newsletter-head">
    <h3>NEWSLETTER SIGN UP</h3>
    <svg width="16" height="12" viewBox="0 0 16 12"><rect x="0.5" y="0.5" width="15" height="11" fill="none" stroke="#f39a1f"/><path d="M1 1l7 6 7-6" fill="none" stroke="#f39a1f"/></svg>
  </div>
  <p class="newsletter-text">Lorem ipsum dolor sit amet, consectetur adipiscing elit, sed do eiusmod tempor incididunt ut labore et dolore magna.</p>
  <div class="signup">
    <div class="field">Enter your email address</div>
    <span class="btn">SIGN UP</span>
  </div>
</section>

<footer class="site-footer">
  <div class="footer-cols">
    <div class="footer-col">
      <h4>UPCOMING EVENTS</h4>
      <div class="event"><div class="event-thumb"></div><p>Duis aute irure dolor in<br>12 June, Saturday 8pm</p></div>
      <div class="event"><div class="event-thumb"></div><p>Duis aute irure dolor in<br>19 June, Saturday 8pm</p></div>
      <div class="event"><div class="event-thumb"></div><p>Duis aute irure dolor in<br>26 June, Saturday 8pm</p></div>
    </div>
    <div class="footer-col">
      <h4>LATEST POSTS</h4>
      <div class="post"><span class="post-box"></span><p>Phasellus porta fusce suscipit varius mi. Cum sociis natoque penatibus et magnis.</p></div>
      <div class="post"><span class="post-box"></span><p>Phasellus porta fusce suscipit varius mi. Cum sociis natoque penatibus et magnis.</p></div>
      <div class="post"><span class="post-box"></span><p>Phasellus porta fusce suscipit varius mi. Cum sociis natoque penatibus et magnis.</p></div>
    </div>
    <div class="footer-col">
      <h4>QUICK LINK</h4>
      <ul class="links"><li>HOME</li><li>MUSIC</li><li>ABOUT US</li><li>VIDEOS</li><li>CONTACT US</li></ul>
    </div>
    <div class="footer-col">
      <h4>CONTACT US</h4>
      <div class="contact-row"><svg width="8" height="10" viewBox="0 0 8 10"><path d="M4 0a4 4 0 0 0-4 4c0 3 4 6 4 6s4-3 4-6a4 4 0 0 0-4-4z" fill="#f39a1f"/><circle cx="4" cy="4" r="1.4" fill="#181818"/></svg><span>P.O. Box 2140,<br>Lindmar Town 8021</span></div>
      <div class="contact-row"><svg width="8" height="8" viewBox="0 0 8 8"><path d="M1 0h2l1 2-1 1a5 5 0 0 0 2 2l1-1 2 1v2c0 .5-.5 1-1 1A7 7 0 0 1 0 1c0-.5.5-1 1-1z" fill="#f39a1f"/></svg><span>Help: +41 (0) 555 0142</span></div>
      <div class="contact-row"><svg width="9" height="7" viewBox="0 0 9 7"><rect x=".5" y=".5" width="8" height="6" fill="none" stroke="#f39a1f"/><path d="M.5.5l4 3 4-3" fill="none" stroke="#f39a1f"/></svg><span>info@krelvomi.com</span></div>
    </div>
  </div>
  <div class="copyright">All Rights Reserved. Copyright © 2015</div>
</footer>
</body>
</html>
```